Profesional personal website needs design and business card

I need a business card with my professional name as a logo "Dorian Vitality" for my business. I am a Wellness Coach, consultant and trainer. So it should be professional, wellness oriented and modern.

Target Market(s)

Private clients, governments, corporations. Luxury and high market.

Industry/Entity Type

Health And Wellness

Contact Information for Business Card

Dorian Vitality should be the logo

Colors

Designer to choose colors to be used in the design.

Requirements
Must have
• Dorian Vitality
• Name: Tomás Lirandel
• Wellness Coach, Consultant & Trainer.
• Website: www.dorianvitality-example.com
• Phone:
• Spain (+34) 612 480 317
• (USA) +1 (555) 610 4829
Nice to have
• The most important is the design of "Dorian Vitality", as this is going to be my personal brand logo. It should be professional, wellness, high end and actual.
Should not have
• no golds, no baroque style..

```html
<!DOCTYPE html>
<html lang="en">
<head>
<meta charset="utf-8">
<title>Dorian Vitality — Business Card</title>
<link href="https://fonts.googleapis.com/css2?family=Arimo:wght@400;700&display=swap" rel="stylesheet">
<style>
  :root {
    --bg: #26272b;
    --card: #ffffff;
    --blue: #1f7fd0;
    --blue-band: #2a8ee0;
    --green: #4fae1e;
    --grey-text: #4a4a4a;
    --rule: #8a8a8a;
    --faint: #e6f0fa;
  }
  * { margin: 0; padding: 0; box-sizing: border-box; }
  html, body { width: 1200px; height: 800px; overflow: hidden; background: var(--bg); }
  body { font-family: "Arimo", Arial, sans-serif; position: relative; }

  .card {
    position: absolute;
    width: 540px; height: 310px;
    background: var(--card);
    border-radius: 18px;
    overflow: hidden;
    box-shadow: 0 20px 40px rgba(0,0,0,.45);
    top: 245px;
  }
  .card--front { left: 40px; }
  .card--back { left: 620px; }

  .brand { display: flex; align-items: center; gap: 12px; }
  .brand__dot { width: 38px; height: 38px; border-radius: 50%; background: var(--blue); flex: none; }
  .brand__name { font-size: 34px; font-weight: 400; color: var(--blue); letter-spacing: .5px; white-space: nowrap; }

  .card--front .brand { position: absolute; left: 50%; top: 50%; transform: translate(-50%, -50%); }

  .back__mark {
    position: absolute; right: 40px; top: 14px;
    width: 170px; height: 170px; border-radius: 50%;
    background: var(--faint);
  }
  .card--back .brand { position: absolute; left: 32px; top: 58px; }
  .card--back .brand__name { font-size: 30px; }

  .person { position: absolute; left: 32px; top: 150px; }
  .person__name { font-size: 22px; font-weight: 700; color: var(--blue); }
  .person__role { font-size: 13px; color: var(--grey-text); margin-top: 3px; }

  .rule { position: absolute; left: 32px; right: 32px; top: 222px; height: 1px; background: var(--rule); }

  .phone { position: absolute; display: flex; align-items: center; gap: 7px; font-size: 13px; color: var(--grey-text); }
  .phone svg { width: 14px; height: 14px; flex: none; }
  .phone--usa { right: 32px; top: 198px; }
  .phone--spain { left: 32px; top: 236px; }

  .band-green { position: absolute; left: 0; right: 0; bottom: 0; height: 9px; background: var(--green); }
  .band-blue {
    position: absolute; right: 0; bottom: 0; width: 220px; height: 40px;
    background: linear-gradient(90deg, var(--blue), var(--blue-band));
    color: #fff; font-size: 12px;
    display: flex; align-items: center; justify-content: center;
  }
</style>
</head>
<body>
  <section class="card card--front" aria-label="Card front">
    <div class="brand">
      <span class="brand__dot"></span>
      <span class="brand__name">Dorian Vitality</span>
    </div>
  </section>

  <section class="card card--back" aria-label="Card back">
    <div class="back__mark"></div>
    <div class="brand">
      <span class="brand__dot"></span>
      <span class="brand__name">Dorian Vitality</span>
    </div>

    <div class="person">
      <p class="person__name">Tomás Lirandel</p>
      <p class="person__role">Coach, Consultant &amp; Trainer.</p>
    </div>

    <div class="phone phone--usa">
      <svg viewBox="0 0 14 14" aria-hidden="true"><circle cx="7" cy="7" r="7" fill="var(--blue)"/><path d="M4.6 3.8c.4-.3.8-.2 1 .2l.5 1c.1.3 0 .6-.2.8l-.4.3c.4.9 1 1.5 1.9 1.9l.3-.4c.2-.2.5-.3.8-.2l1 .5c.4.2.5.6.2 1-.5.8-1.3 1-2.2.6-1.6-.7-2.8-1.9-3.5-3.5-.4-.9-.2-1.7.6-2.2z" fill="#fff"/></svg>
      <span>(USA) +1 (555) 610 4829</span>
    </div>

    <div class="rule"></div>

    <div class="phone phone--spain">
      <svg viewBox="0 0 14 14" aria-hidden="true"><circle cx="7" cy="7" r="7" fill="var(--blue)"/><path d="M4.6 3.8c.4-.3.8-.2 1 .2l.5 1c.1.3 0 .6-.2.8l-.4.3c.4.9 1 1.5 1.9 1.9l.3-.4c.2-.2.5-.3.8-.2l1 .5c.4.2.5.6.2 1-.5.8-1.3 1-2.2.6-1.6-.7-2.8-1.9-3.5-3.5-.4-.9-.2-1.7.6-2.2z" fill="#fff"/></svg>
      <span>Spain (+34) 612 480 317</span>
    </div>

    <div class="band-green"></div>
    <div class="band-blue">www.dorianvitality-example.com</div>
  </section>
</body>
</html>
```